Business card for law firm

Need business card for new law firm. Think confident, authoritative, conservative, but not stuffy or old-fashioned.

Contact Information for Business Card

Content for card - logo (uploaded), plus the following:

Paul Whitcombe (larger font)
Managing Partner (larger font, but not as large as name)
Level 9, 7 Ferris Lane
Sydney NSW 2000
Main Tel 02 9364 2710
Direct Tel 02 8472 3159
Email paul@qvlegal.com.au
www.qvlegal.com.au

Letterhead design should include logo plus:
Level 9, 7 Ferris Lane
Sydney NSW 2000
Tel 02 8472 3159
www.qvlegal.com.au

```html
<!DOCTYPE html>
<html lang="en">
<head>
<meta charset="utf-8">
<title>Quayvale Legal – Business Card</title>
<link href="https://fonts.googleapis.com/css2?family=Open+Sans:wght@400;600;700&display=swap" rel="stylesheet">
<style>
  :root {
    --navy: #0c1d55;
    --ink: #111111;
    --paper: #ffffff;
    --stage: #d6d7d9;
    --black-card: #000000;
    --muted: #222222;
  }
  * { margin: 0; padding: 0; box-sizing: border-box; }
  html, body {
    width: 1200px; height: 1142px; overflow: hidden;
    background: var(--stage);
    font-family: "Open Sans", Arial, sans-serif;
  }
  .card {
    position: absolute;
    width: 758px; height: 434px;
    border-radius: 36px;
    overflow: hidden;
  }
  .card--front { left: 367px; top: 93px; background: var(--paper); border: 1px solid #b9babc; }
  .card--back { left: 76px; top: 593px; background: var(--black-card); }

  .wordmark {
    position: absolute; left: 0; right: 0;
    text-align: center; font-weight: 400;
    line-height: 1;
  }
  .wordmark__name { display: block; letter-spacing: 2px; }
  .wordmark__sub { display: block; letter-spacing: 20px; padding-left: 20px; margin-top: 14px; }

  .card--front .wordmark { top: 140px; color: var(--ink); }
  .card--front .wordmark__name { font-size: 44px; }
  .card--front .wordmark__sub { font-size: 15px; }

  .card--back .wordmark { top: 222px; color: var(--paper); }
  .card--back .wordmark__name { font-size: 52px; }
  .card--back .wordmark__sub { font-size: 19px; letter-spacing: 26px; padding-left: 26px; }

  .holder {
    position: absolute; top: 228px; left: 0; right: 0;
    text-align: center; font-size: 20px; color: var(--ink);
  }
  .holder__name { color: var(--navy); font-weight: 700; font-size: 24px; }

  .swoosh { position: absolute; left: 0; top: 0; width: 758px; height: 434px; }

  .contact {
    position: absolute; left: 0; right: 0;
    display: flex; justify-content: center; gap: 16px;
    color: var(--paper); font-size: 20px; line-height: 1;
  }
  .contact__item { display: flex; align-items: center; gap: 6px; }
  .contact__item svg { width: 17px; height: 17px; flex: none; }
  .contact--phones { top: 320px; }
  .contact--web { top: 355px; }
  .contact--address { top: 394px; }

  .web-address {
    position: absolute; top: 366px; left: 0; right: 0;
    text-align: center; color: var(--paper);
    font-size: 24px; letter-spacing: 4px;
  }
  .web-address strong { font-weight: 700; }
</style>
</head>
<body>

<section class="card card--front" aria-label="Card front">
  <div class="wordmark">
    <span class="wordmark__name">QUAYVALE</span>
    <span class="wordmark__sub">LEGAL</span>
  </div>

  <p class="holder"><span class="holder__name">Paul Whitcombe,</span> Managing Partner</p>

  <svg class="swoosh" viewBox="0 0 758 434" aria-hidden="true">
    <path d="M18 348 Q379 188 742 352 Q379 206 18 348 Z" fill="var(--ink)"/>
    <path d="M0 356 Q379 216 758 356 L758 434 L0 434 Z" fill="var(--navy)"/>
  </svg>

  <div class="contact contact--phones">
    <span class="contact__item">
      <svg viewBox="0 0 16 16"><circle cx="8" cy="8" r="7" fill="none" stroke="#fff" stroke-width="1.3"/><path d="M5.5 4.5 L7 6 L6.2 7 Q7 9 9 9.8 L10 9 L11.5 10.5 L10.5 11.6 Q6 11 4.4 5.5 Z" fill="#fff"/></svg>
      02 9364 2710(Main)
    </span>
    <span class="contact__item">
      <svg viewBox="0 0 16 16"><circle cx="8" cy="8" r="7" fill="none" stroke="#fff" stroke-width="1.3"/><path d="M5.5 4.5 L7 6 L6.2 7 Q7 9 9 9.8 L10 9 L11.5 10.5 L10.5 11.6 Q6 11 4.4 5.5 Z" fill="#fff"/></svg>
      02 8472 3159(Direct)
    </span>
  </div>

  <div class="contact contact--web">
    <span class="contact__item">
      <svg viewBox="0 0 16 16"><path d="M1 6 L8 2 L15 6 L15 14 L1 14 Z" fill="#fff"/><path d="M1 6 L8 10 L15 6" fill="none" stroke="var(--navy)" stroke-width="1.3"/></svg>
      paul@qvlegal.com.au
    </span>
    <span class="contact__item">
      <svg viewBox="0 0 16 16" fill="none" stroke="#fff" stroke-width="1.2"><circle cx="8" cy="8" r="6.5"/><ellipse cx="8" cy="8" rx="3" ry="6.5"/><path d="M1.5 8 H14.5 M2.5 4.8 H13.5 M2.5 11.2 H13.5"/></svg>
      www.qvlegal.com.au
    </span>
  </div>

  <div class="contact contact--address">
    <span class="contact__item">Level 9, 7 Ferris Lane, Sydney NSW 2000</span>
  </div>
</section>

<section class="card card--back" aria-label="Card back">
  <div class="wordmark">
    <span class="wordmark__name">QUAYVALE</span>
    <span class="wordmark__sub">LEGAL</span>
  </div>
  <p class="web-address">www.<strong>qvlegal</strong>.com.au</p>
</section>

</body>
</html>
```